Fast Growing Personal Injury Law Firm Needs Business Card Design

We need a business card design for a fast growing personal injury law firm in Florida. Our name is Dorian Kalvenfeld, P.A. Our practice is comprised of younger attorneys (in their 30s) that employ more modern techniques/tools than our older competition. We would prefer a look that is a modern play on a classic look. Also, we would like to continue using a color scheme that employs navy blue and kelly green (other shades of green could be fine too) as well as our "E" logo.

Industry/Entity Type

Law Firm

```html
<!DOCTYPE html>
<html lang="en">
<head>
<meta charset="UTF-8">
<title>Dorian Kalvenfeld, P.A. – Business Card</title>
<link rel="stylesheet" href="https://fonts.googleapis.com/css2?family=Crimson+Text:wght@400;600&family=Open+Sans:wght@400;700&display=swap">
<style>
  :root {
    --navy: #1f2466;
    --navy-deep: #15184d;
    --navy-light: #2c3280;
    --green: #1f8a3b;
    --paper: #ffffff;
    --ink: #3c3c3c;
    --ink-soft: #5a5a5a;
    --backdrop: #e9eaee;
  }
  * { box-sizing: border-box; margin: 0; padding: 0; }
  html, body { width: 1200px; height: 900px; overflow: hidden; }
  body {
    background: var(--backdrop);
    font-family: "Open Sans", Arial, sans-serif;
    position: relative;
  }
  .card {
    position: absolute;
    left: 320px;
    width: 560px;
    height: 320px;
    border-radius: 4px;
    overflow: hidden;
    box-shadow: 0 6px 18px rgba(20, 24, 60, 0.18);
  }
  /* Back side */
  .card-back {
    top: 90px;
    background: linear-gradient(135deg, var(--navy-light) 0%, var(--navy) 55%, var(--navy-deep) 100%);
  }
  .card-back .firm {
    position: absolute;
    right: 36px;
    bottom: 46px;
    text-align: left;
    color: var(--paper);
    font-family: "Crimson Text", Georgia, serif;
  }
  .card-back .firm-name { font-size: 24px; font-weight: 600; line-height: 1.1; }
  .card-back .firm-tag { font-size: 17px; letter-spacing: 1px; }

  /* Front side */
  .card-front {
    top: 480px;
    background: var(--paper);
  }
  .brand {
    position: absolute;
    left: 30px;
    top: 26px;
    display: flex;
    align-items: center;
    gap: 10px;
    font-family: "Crimson Text", Georgia, serif;
  }
  .brand-mark {
    width: 38px; height: 38px;
    background: var(--navy);
  }
  .brand-name { color: var(--navy); font-size: 25px; font-weight: 600; line-height: 1; }
  .brand-tag { color: var(--green); font-size: 18px; letter-spacing: 2.2px; line-height: 1.1; }

  .person {
    position: absolute;
    left: 30px;
    top: 140px;
  }
  .person-name { color: var(--navy); font-size: 24px; font-weight: 700; line-height: 1.1; }
  .person-title { color: var(--ink-soft); font-size: 14px; margin-bottom: 14px; }
  .person-address { color: var(--ink); font-size: 15px; line-height: 1.45; font-style: normal; }

  .contacts {
    position: absolute;
    left: 318px;
    top: 150px;
    list-style: none;
    color: var(--ink);
    font-size: 15px;
    line-height: 1.45;
  }
  .contacts li { display: flex; align-items: center; gap: 6px; }
  .contacts svg { width: 12px; height: 12px; fill: var(--navy); flex: none; }

  .footer-bands { position: absolute; left: 0; bottom: 0; width: 560px; height: 48px; }
</style>
</head>
<body>

<section class="card card-back" aria-label="Card back">
  <div class="firm">
    <p class="firm-name">Dorian Kalvenfeld, P.A.</p>
    <p class="firm-tag">Personal Injury Attorneys</p>
  </div>
</section>

<section class="card card-front" aria-label="Card front">
  <header class="brand">
    <span class="brand-mark"></span>
    <div>
      <p class="brand-name">Dorian Kalvenfeld, P.A.</p>
      <p class="brand-tag">Personal Injury Attorneys</p>
    </div>
  </header>

  <div class="person">
    <p class="person-name">Owen Hartley</p>
    <p class="person-title">Managing Member</p>
    <address class="person-address">1187 Meridian Lane,<br>Orlando, FL 32801</address>
  </div>

  <ul class="contacts">
    <li><svg viewBox="0 0 12 12"><path d="M2.5 1 L4.5 1 L5.2 3.5 L4 4.5 Q5 7 7.5 8 L8.5 6.8 L11 7.5 L11 9.5 Q10.5 11 9 11 Q1 10 1 2.5 Q1 1 2.5 1Z"/></svg>(407) 555-0142</li>
    <li><svg viewBox="0 0 12 12"><rect x="3" y="1" width="6" height="4"/><rect x="1" y="5" width="10" height="6" rx="1"/></svg>(407) 555-0143</li>
    <li><svg viewBox="0 0 12 12"><path d="M3.5 0.5h5a1 1 0 0 1 1 1v9a1 1 0 0 1-1 1h-5a1 1 0 0 1-1-1v-9a1 1 0 0 1 1-1zM4 2v7h4V2z"/></svg>(407) 555-0187</li>
    <li><svg viewBox="0 0 12 12"><path d="M0.5 2.5h11v7h-11z M1 3l5 4 5-4" stroke="#fff" stroke-width="0.8"/></svg>owen@kalvenfeld.com</li>
    <li><svg viewBox="0 0 12 12"><circle cx="6" cy="6" r="5.5"/><path d="M0.5 6h11 M6 0.5v11 M6 0.5q-3 5.5 0 11 M6 0.5q3 5.5 0 11" stroke="#fff" stroke-width="0.7" fill="none"/></svg>www.kalvenfeld.com</li>
  </ul>

  <svg class="footer-bands" viewBox="0 0 560 48" aria-hidden="true">
    <polygon points="0,10 222,10 232,24 560,24 560,48 0,48" fill="var(--navy)"/>
    <polygon points="252,12 378,12 372,22 246,22" fill="var(--green)"/>
    <polygon points="392,12 478,12 472,22 386,22" fill="var(--navy)"/>
    <polygon points="492,12 560,12 560,22 486,22" fill="var(--green)"/>
  </svg>
</section>

</body>
</html>
```